A Label for an ECO Friendly Spirit Company

Design a label which can be used for vodka and gin (London Dry Gin). It should be Square type Like the Shape File you see in the uploads. KIRO means Kind Inventive Rare and Original. We want a cool and slim label that calls for eco-friendly. We want to use it for our premium
Vodka and our London Dry Gin. Please use the logo and design it in Square Type.

40%vol, 700ml

Target Market(s)

spirits and events

Industry/Entity Type

SPIRITS

Colors
00AB8E
00BBA5
67D7C9
C6EFE9
E9F9F6
59FF00
82FF00
B8FF75
E3FFCB
F4FFEA

Requirements
Must have
• Logo from KIRO, Squaee Shape

```html
<!DOCTYPE html>
<html lang="en">
<head>
<meta charset="utf-8">
<title>KIRO Vodka – Square Label</title>
<link rel="stylesheet" href="https://fonts.googleapis.com/css2?family=Antonio:wght@100;700&display=swap">
<style>
  :root {
    --label-green: #04331f;
    --label-ink: #f6f7f2;
  }
  html, body {
    margin: 0;
    padding: 0;
    width: 1200px;
    height: 1200px;
    overflow: hidden;
    background: var(--label-green);
  }
  .label {
    display: block;
    width: 1200px;
    height: 1200px;
    background: var(--label-green);
  }
  .brand-name {
    font-family: "Antonio", "Arial Narrow", sans-serif;
    font-weight: 100;
    fill: var(--label-ink);
  }
  .product-type {
    font-family: "Antonio", "Arial Narrow", sans-serif;
    font-weight: 700;
    fill: var(--label-ink);
  }
  .volume-info {
    font-family: "Antonio", "Arial Narrow", sans-serif;
    font-weight: 700;
    fill: var(--label-ink);
  }
</style>
</head>
<body>
  <svg class="label" viewBox="0 0 1200 1200" xmlns="http://www.w3.org/2000/svg" role="img" aria-label="KIRO Vodka label, 40% vol, 700 ml">
    <text class="brand-name" x="330" y="783" font-size="470" textLength="542" lengthAdjust="spacingAndGlyphs">KIRO</text>
    <text class="product-type" x="600" y="880" font-size="78" text-anchor="middle" textLength="168" lengthAdjust="spacingAndGlyphs">VODKA</text>
    <text class="volume-info" x="600" y="1044" font-size="37" text-anchor="middle" textLength="224" lengthAdjust="spacingAndGlyphs">40% VOL, 700ML</text>
  </svg>
</body>
</html>
```